Wordpress Theme for Medical Clinics

** Please view updated Sitemap2.pdf doc to clarify some confusion ***

This is a multiuser WordPress subscription site for medical clinics. Please see attachment for sitemap. Please do not include extra content like social media icons, search bars, or images. If you have questions, please ask for clarification.
The site contains the following pages and sub-pages:

1. Home
2. Our Clinic
2a. Our Clinic > Mission
2b. Our Clinic > Services
2c. Our Clinic > Clinic Policies
2d. Our Clinic > Schedules
3. Our Staff
3a. Our Staff > [Staff member page]
4. Resources
4a. Resources > Patient Health (index)
4b. Resources > Patient Health (index) > [post]
4c. Resources > Links
4d. Resources > Forms
5. Alerts
5a. Alerts > [Alert Page]
6. Contact Us

Includes the Following Pages, Subpages, and Content
1. Home
a. About Us
b. Our Staff
c. Bulletins
d. Accepting New Patients (shown as an alert widget)
e. Links
i. Physician Toolbox
ii. Book an Appointment
f. Clinic Policies
i. Show first 3 policies (e.g. Late Arrivals, Missed Appointments, Fees)
ii. Link to Clinic Policies page
g. Primary widget (displayed on all pages)
i. Hours of operation
ii. Contact Info
1. Tel
2. Fax
3. Email
4. Address
5. Get directions (link to Google Maps)
2. Our Clinic
a. Main Page
i. Clinic Name
ii. Overview
iii. Languages Spoken
iv. Secondary Navigation
1. Mission
2. Services
3. Clinic Policies
4. Schedules (see attachment)
b. Our Clinic > Mission
c. Our Clinic > Services
i. For each service include service TITLE and DESCRIPTION
d. Our Clinic > Clinic Policies
i. For each policy include policy TITLE and DESCRIPTION
ii. Include the following policies in mockup
1. Late arrivals
2. Missed appointments
3. Fees for missed appointments
4. Referrals and follow-ups
5. Services not covered by RDA
6. Information for LTF patients
7. Medical Legal Reports
e. Our Clinic > Schedules
3. Our Staff
a. Main Page
i. Display a list of staff members. Include NAME and DESIGNATION
b. Our Staff > [Staff Name]
i. Include NAME, PICTURE, DESIGNATION, and BIO
4. Resources
a. Resources > Patient Health
i. Main Page
1. Posts (ordered by date)
a. Title
b. Summary
2. Side Navigation
a. Post Categories
ii. Patient Health > [post title]
1. Title
2. Post Category
3. Date
4. Author
5. Summary
6. Body
b. Resources > Links
1. Secondary Navigation - Categories
a. Sample Categories:
i. Local Services
ii. RDA and Drug Coverage
iii. Mental Health Resources
2. Category page
a. Include the following links in the 'Local Services' category
i. Hypertension clinics
ii. Home Care services
iii. Vaccine Clinics
c. Resources > Forms
i. Display a table with form TITLE and CATEGORY
ii. Side Navigation
1. Form Categories
a. Use the following sample Categories
i. Referrals
ii. Insurance
iii. Intake
iv. Discharge
v. Waivers
5. Alerts
a. Main page
i. List of all Alert posts
1. Include post TITLE as a link to the post
ii. Side Navigation
1. Alerts Archive
a. shown as Month + Number of posts
iii. Alerts > [Alert page]
1. Include TITLE, DATE, AUTHOR, BODY
6. Contact Us
a. Map
b. Hours of operation
c. Address
d. Phone number
e. Fax number
e. Fax number
f. Map
g. Email

Design notes:
- fixed width
- responsive (need designs for mobile, tablet, and desktop)
- simple, dark font, white background
- use Font Awesome icons where needed
- user adds own logo

Target Market(s)

Medical Clinics

Industry/Entity Type

Medical

Number of Pages Required

5+ page

Font styles to use
Serif
Sans Serif

Requirements
Must have
• Please keep designs very simple.
• Examples:
• https://www.quolbin.com/install
• http://www.ventrohax.com/company/about-us
• http://brindlequota.org/
• http://www.trosk.com/
Should not have
• Minimal or no use of shadows and gradients

```html
<!DOCTYPE html>
<html lang="en">
<head>
<meta charset="utf-8">
<title>Clinic Site</title>
<link href="https://fonts.googleapis.com/css2?family=Raleway:wght@600;700;800&family=Arimo:wght@400;700&display=swap" rel="stylesheet">
<style>
:root{
  --blue:#5ba3dc;
  --blue-dark:#4a8bc4;
  --green:#41d6a9;
  --text:#555;
  --line:#dcdcdc;
  --white:#fff;
}
*{margin:0;padding:0;box-sizing:border-box}
html,body{width:793px;height:1200px;overflow:hidden}
body{position:relative;background:var(--white);font-family:"Arimo",Arial,sans-serif;color:var(--text);font-size:9.5px}
.abs{position:absolute}
h2{font-family:"Raleway",sans-serif;font-weight:700;color:var(--blue);font-size:17px}
a{color:inherit}
.topbar{left:0;top:0;width:793px;height:33px;background:var(--blue);color:var(--white);font-size:9.5px}
.topbar .contact{left:70px;top:13px}
.topbar .book{left:626px;top:9px}
.navbar{left:0;top:33px;width:793px;height:49px;background:var(--green)}
.brand{left:66px;top:12px;font-family:"Raleway",sans-serif;font-weight:800;font-size:23px;color:var(--white);letter-spacing:.3px}
.nav a{position:absolute;top:20px;color:var(--white);font-size:9.5px;text-decoration:none;letter-spacing:.2px}
.band{left:0;top:82px;width:793px;height:159px;background:var(--blue)}
.slider{left:66px;top:98px;width:661px;height:266px;background:var(--white);border:1px solid #e4e4e4;padding:3px}
.slide-img{width:100%;height:100%;background:linear-gradient(100deg,#bfe8f6 0%,#e6f6fb 40%,#f4f7fa 60%,#d4ecf5 100%);position:relative}
.caption{position:absolute;left:0;bottom:0;width:100%;height:64px;background:rgba(60,70,80,.72);color:var(--white);font-size:9.6px;line-height:13.3px;padding:14px 0 0 10px}
.arrow{position:absolute;top:112px}
.photo{border:1px solid #e0e0e0;background:var(--white);padding:3px}
.photo div{width:100%;height:100%}
.intro{left:262px;top:420px;width:226px;line-height:13.3px;text-align:justify;font-size:9.5px}
.intro p+p{margin-top:13px}
.box{border:1px solid var(--line);background:var(--white)}
.list{list-style:none}
.list li{position:relative;padding-left:11px;height:19.8px;font-size:9.5px}
.list li::before{content:"";position:absolute;left:1px;top:2px;border-left:4px solid var(--blue);border-top:3px solid transparent;border-bottom:3px solid transparent}
.btn{display:inline-block;background:var(--blue);color:var(--white);font-size:9.5px;padding:3px 5px}
.alert h3{font-family:"Raleway",sans-serif;font-weight:700;font-size:10.5px;color:var(--blue);margin-bottom:7px}
.alert p{font-size:8.6px;line-height:13.3px;color:#444}
.alert a{font-size:8.6px;color:var(--blue);text-decoration:none}
.hours{left:513px;top:391px;width:214px;height:276px;background:var(--blue);color:var(--white);font-size:9.4px}
.hours h2,.newp h2,.foot h2{color:var(--white)}
.row{position:absolute;left:0;width:100%}
.newp{left:513px;top:684px;width:214px;height:49px;background:var(--green);color:var(--white)}
.foot{left:0;top:981px;width:793px;height:186px;background:var(--blue);color:var(--white);font-size:9.5px}
.foot .list li::before{border-left-color:var(--white)}
.foot .list li{height:15.9px}
.copy{left:0;top:1167px;width:793px;height:33px;background:var(--blue-dark);color:var(--white);font-size:9.5px;text-align:center;padding-top:12px}
</style>
</head>
<body>

<div class="abs topbar">
  <span class="abs contact">Telephone 0321657700 &nbsp;|&nbsp; Email contact@clinsite.ca</span>
  <span class="abs book">Book an Appointment</span>
</div>

<header class="abs navbar">
  <div class="abs brand">CLINIC SITE</div>
  <nav class="nav">
    <a style="left:270px">HOME</a>
    <a style="left:335px">OUR CLINIC</a>
    <a style="left:428px">STAFF</a>
    <a style="left:494px">RESOURCES</a>
    <a style="left:590px">ALERTS</a>
    <a style="left:664px">CONTACT US</a>
  </nav>
</header>

<div class="abs band"></div>

<section class="abs slider">
  <div class="slide-img" role="img" aria-label="Doctor in a white coat holding a stethoscope over a light blue heartbeat background">
    <svg class="arrow" style="left:9px" width="38" height="38" viewBox="0 0 38 38"><circle cx="19" cy="19" r="16.5" fill="none" stroke="#555" stroke-width="3"/><path d="M22 11 L14 19 L22 27" fill="none" stroke="#555" stroke-width="3.5"/></svg>
    <svg class="arrow" style="left:612px" width="38" height="38" viewBox="0 0 38 38"><circle cx="19" cy="19" r="16.5" fill="none" stroke="#555" stroke-width="3"/><path d="M16 11 L24 19 L16 27" fill="none" stroke="#555" stroke-width="3.5"/></svg>
    <div class="caption">Lorem Ipsum is simply dummy text of the printing and typesetting industry. Lorem Ipsum has been the industry's standard dummy text ever since the<br>1500s, when an unknown printer took a galley of type and scrambled it to make.It has survived not only five centuries, but also the leap into electronic<br>typesetting, remaining essentially unchanged. It was popularised in the 1960.</div>
  </div>
</section>

<h2 class="abs" style="left:70px;top:388px">Our Clinic</h2>
<div class="abs photo" style="left:66px;top:420px;width:182px;height:130px">
  <div role="img" aria-label="Doctor holding a clipboard in a bright office" style="background:linear-gradient(90deg,#d7d9d8,#eef0ef 60%,#c9cccb)"></div>
</div>
<div class="abs intro">
  <p>Lorem Ipsum is simply dummy text of the printing and typesetting industry. Lorem Ipsum has been the industry's standard dummy text ever since the 1500s, when an unknown printer took a galley of type and scrambled it to make.</p>
  <p>It has survived not only five centuries, but also the leap into electronic typesetting, remaining essentially unchanged. It was popularised in the 1960.</p>
</div>

<section class="abs box" style="left:67px;top:574px;width:195px;height:152px">
  <h2 class="abs" style="left:9px;top:9px">Staff</h2>
  <ul class="abs list" style="left:9px;top:42px">
    <li>Dr john Smith MD</li><li>Dr jane doe MD</li><li>Dr Bruce Almghty MD</li><li>Dr jhon Smith MD</li>
  </ul>
  <span class="abs btn" style="left:12px;top:129px">View All &raquo;</span>
</section>

<section class="abs box" style="left:293px;top:574px;width:195px;height:152px">
  <h2 class="abs" style="left:14px;top:9px">Links</h2>
  <ul class="abs list" style="left:14px;top:42px">
    <li>Radiology Clinics</li><li>Physotherapy Clinics</li><li>LTF Clinics</li><li>NVIC Clinics</li>
  </ul>
  <span class="abs btn" style="left:17px;top:129px">View All &raquo;</span>
</section>

<h2 class="abs" style="left:77px;top:766px">Alerts</h2>
<div class="abs photo" style="left:75px;top:802px;width:105px;height:62px">
  <div role="img" aria-label="Business people in a modern office" style="background:linear-gradient(90deg,#8a9094,#c6cacc,#6e7275)"></div>
</div>
<div class="abs alert" style="left:191px;top:804px;width:290px">
  <h3>Alert Headline 1</h3>
  <p>Lorem ipsum dolor sit amet, consectetuer a iscing elit. Aenean commodo ligula eget dolo. Aenean massa. Cum sociis natoque penatibet</p>
  <a>Read more...</a>
</div>
<div class="abs photo" style="left:75px;top:887px;width:105px;height:62px">
  <div role="img" aria-label="Hands working at a laptop in a meeting" style="background:linear-gradient(90deg,#4d4f52,#b9bcbf,#3e4043)"></div>
</div>
<div class="abs alert" style="left:193px;top:888px;width:290px">
  <h3>Alert Headline 2</h3>
  <p>Lorem ipsum dolor sit amet, consectetuer a iscing elit. Aenean commodo ligula eget dolo. Aenean massa. Cum sociis natoque penatibet</p>
  <a>Read more...</a>
</div>

<aside class="abs hours">
  <h2 class="abs" style="left:11px;top:10px">Hours Of Opration</h2>
  <div class="row" style="top:40px"><span class="abs" style="left:20px">Monday</span><span class="abs" style="left:108px">8:00 AM - 6:00 PM</span></div>
  <div class="row" style="top:56px"><span class="abs" style="left:20px">Tusday</span><span class="abs" style="left:108px">8:00 AM - 6:00 PM</span></div>
  <div class="row" style="top:72px"><span class="abs" style="left:20px">Wednesday</span><span class="abs" style="left:108px">8:00 AM - 6:00 PM</span></div>
  <div class="row" style="top:88px"><span class="abs" style="left:20px">Thursday</span><span class="abs" style="left:108px">8:00 AM - 6:00 PM</span></div>
  <div class="row" style="top:103px"><span class="abs" style="left:20px">Friday</span><span class="abs" style="left:108px">8:00 AM - 6:00 PM</span></div>
  <div class="row" style="top:119px"><span class="abs" style="left:20px">Saturday</span><span class="abs" style="left:108px">8:00 AM - 4:00 PM</span></div>
  <div class="row" style="top:135px"><span class="abs" style="left:20px">Sunday</span><span class="abs" style="left:108px">8:00 AM - 4:00 PM</span></div>
  <a class="abs" style="left:20px;top:151px;text-decoration:underline">Holiday hours</a>
  <span class="abs" style="left:19px;top:175px">CONTACT INFO</span>
  <div class="row" style="top:195px"><span class="abs" style="left:17px">Telephone</span><span class="abs" style="left:123px">8045550190</span></div>
  <div class="row" style="top:211px"><span class="abs" style="left:17px">Email</span><span class="abs" style="left:123px">contact@clinsite.ca</span></div>
  <div class="row" style="top:227px"><span class="abs" style="left:17px">Address</span><span class="abs" style="left:123px;line-height:10.8px">48 Harbour Lane<br>Lakeview B.C<br>Canada V2K4R7</span></div>
</aside>

<aside class="abs newp">
  <h2 class="abs" style="left:10px;top:7px">New Patients</h2>
  <span class="abs" style="left:12px;top:31px">Accepting New Patients &nbsp;<a style="text-decoration:underline">Contact US</a></span>
</aside>

<aside class="abs box" style="left:513px;top:750px;width:214px;height:208px">
  <h2 class="abs" style="left:13px;top:10px">Clinic Polices</h2>
  <ul class="abs list" style="left:15px;top:43px">
    <li>Late Arrivals</li><li>Missed Appointments</li><li>Fees for Missed Appointment</li><li>Referrals and follow ups</li><li>Services not covered by RDA</li><li>Information for LTF Patients</li><li>Medicial Legal Reports</li>
  </ul>
  <span class="abs btn" style="left:16px;top:185px">View All &raquo;</span>
</aside>

<footer class="abs foot">
  <h2 class="abs" style="left:76px;top:14px">Our Clinic</h2>
  <ul class="abs list" style="left:78px;top:41px">
    <li>Mission</li><li>Services</li><li>Schdules</li><li>Polices</li><li>Staff</li><li>Alerts</li><li>Contact us</li>
  </ul>
  <h2 class="abs" style="left:202px;top:14px">Resources</h2>
  <ul class="abs list" style="left:204px;top:42px">
    <li>Our &nbsp;Clinic</li><li>Mission</li><li>Services</li>
  </ul>
  <h2 class="abs" style="left:340px;top:13px">Hours Of Oprations</h2>
  <div class="row" style="top:42px"><span class="abs" style="left:342px">Monday</span><span class="abs" style="left:429px">8:00 AM - 6:00 PM</span></div>
  <div class="row" style="top:58px"><span class="abs" style="left:342px">Tusday</span><span class="abs" style="left:429px">8:00 AM - 6:00 PM</span></div>
  <div class="row" style="top:74px"><span class="abs" style="left:342px">Wednesday</span><span class="abs" style="left:429px">8:00 AM - 6:00 PM</span></div>
  <div class="row" style="top:90px"><span class="abs" style="left:342px">Thursday</span><span class="abs" style="left:429px">8:00 AM - 6:00 PM</span></div>
  <div class="row" style="top:106px"><span class="abs" style="left:342px">Friday</span><span class="abs" style="left:429px">8:00 AM - 6:00 PM</span></div>
  <div class="row" style="top:121px"><span class="abs" style="left:342px">Saturday</span><span class="abs" style="left:429px">8:00 AM - 4:00 PM</span></div>
  <div class="row" style="top:137px"><span class="abs" style="left:342px">Sunday</span><span class="abs" style="left:429px">8:00 AM - 4:00 PM</span></div>
  <a class="abs" style="left:342px;top:153px;text-decoration:underline">Holiday hours</a>
  <h2 class="abs" style="left:575px;top:14px">Contact us</h2>
  <svg class="abs" style="left:581px;top:45px" width="12" height="12" viewBox="0 0 24 24"><path fill="#fff" d="M6.6 10.8a15 15 0 0 0 6.6 6.6l2.2-2.2a1 1 0 0 1 1-.25 11.4 11.4 0 0 0 3.6.57 1 1 0 0 1 1 1V20a1 1 0 0 1-1 1A17 17 0 0 1 3 4a1 1 0 0 1 1-1h3.5a1 1 0 0 1 1 1c0 1.25.2 2.45.57 3.6a1 1 0 0 1-.25 1z"/></svg>
  <span class="abs" style="left:607px;top:44px">8045550190</span>
  <svg class="abs" style="left:580px;top:70px" width="18" height="12" viewBox="0 0 18 12"><rect x=".5" y=".5" width="17" height="11" fill="none" stroke="#fff"/><path d="M.5 .5 L9 7 L17.5 .5 M.5 11.5 L7 5.5 M17.5 11.5 L11 5.5" fill="none" stroke="#fff"/></svg>
  <span class="abs" style="left:607px;top:68px">contact@clinsite.ca</span>
  <svg class="abs" style="left:583px;top:97px" width="14" height="20" viewBox="0 0 14 20"><path fill="#fff" d="M7 0a7 7 0 0 0-7 7c0 5 7 13 7 13s7-8 7-13a7 7 0 0 0-7-7zm0 10a3 3 0 1 1 0-6 3 3 0 0 1 0 6z"/></svg>
  <span class="abs" style="left:607px;top:96px;line-height:10.8px">48 Harbour Lane<br>Lakeview B.C<br>Canada V2K4R7</span>
</footer>

<div class="abs copy">Copyright © 2015 KRT for me and Harbor Division. All Rights Reserved Terms of Use &nbsp;| &nbsp;Privacy Policy &nbsp;| &nbsp;Sitemap</div>

</body>
</html>
```